Vantiqo custom business card design

Need a authentic, innovative business card design for a new mobile app business. I am uploading a few screen images from our app for you to view. I would like app design theme to match business card design. I can also send logo images.

```html
<!DOCTYPE html>
<html lang="en">
<head>
<meta charset="utf-8">
<title>Vantiqo Business Card</title>
<link href="https://fonts.googleapis.com/css2?family=Open+Sans:wght@400;600;800&display=swap" rel="stylesheet">
<style>
  :root {
    --backdrop: #e6e6e8;
    --card: #ffffff;
    --ink: #1c1c1c;
    --purple: #5e0f8b;
    --grey-text: #2a2a2a;
    --muted: #555555;
  }
  * { box-sizing: border-box; margin: 0; padding: 0; }
  html, body {
    width: 1200px; height: 1000px; overflow: hidden;
    background: var(--backdrop);
    font-family: "Open Sans", Arial, sans-serif;
  }
  .stage { position: relative; width: 1200px; height: 1000px; }
  .card {
    position: absolute;
    width: 700px; height: 400px;
    background: var(--card);
    border-radius: 26px;
    box-shadow: 0 10px 30px rgba(0,0,0,0.18);
  }
  /* Back side */
  .card-back { left: 250px; top: 50px; }
  .back-mark {
    position: absolute; left: 0; right: 0; top: 70px;
    display: flex; flex-direction: column; align-items: center;
  }
  .back-dot {
    width: 130px; height: 130px; border-radius: 50%;
    background: var(--purple);
  }
  .back-name {
    margin-top: 26px;
    font-weight: 800; font-size: 58px; line-height: 1;
    color: var(--ink); letter-spacing: -0.5px;
  }
  .back-url {
    margin-top: 18px;
    font-size: 20px; letter-spacing: 6px; color: var(--muted);
  }
  /* Front side */
  .card-front { left: 250px; top: 530px; }
  .front-name {
    position: absolute; left: 42px; top: 34px;
    font-weight: 800; font-size: 56px; line-height: 1;
    color: var(--ink); letter-spacing: -0.5px;
  }
  .person { position: absolute; left: 46px; top: 118px; }
  .person-name {
    font-weight: 800; font-size: 24px; color: var(--purple); line-height: 1.1;
  }
  .person-role { font-size: 16px; color: var(--grey-text); letter-spacing: 0.5px; }
  .address {
    position: absolute; left: 46px; top: 180px;
    font-size: 17px; line-height: 1.3; color: var(--grey-text);
  }
  .contacts {
    position: absolute; left: 46px; top: 232px;
    list-style: none; font-size: 17px; line-height: 25px; color: var(--grey-text);
  }
  .contacts li { display: flex; align-items: center; gap: 10px; height: 25px; }
  .contacts svg { width: 16px; height: 16px; fill: var(--purple); flex: none; }
  .contacts .plain { padding-left: 26px; }
  .front-disc {
    position: absolute; left: 380px; top: 70px;
    width: 290px; height: 290px; border-radius: 50%;
    background: linear-gradient(180deg, #6a1a9a 0%, var(--purple) 100%);
  }
</style>
</head>
<body>
<main class="stage">

  <section class="card card-back" aria-label="Card back">
    <div class="back-mark">
      <div class="back-dot"></div>
      <div class="back-name">Vantiqo</div>
      <div class="back-url">www.vantiqo.com</div>
    </div>
  </section>

  <section class="card card-front" aria-label="Card front">
    <div class="front-name">Vantiqo</div>
    <div class="person">
      <div class="person-name">MARTA LENZ</div>
      <div class="person-role">PRESIDENT</div>
    </div>
    <div class="address">4127 Halden Crescent<br>Brookvale, NY 11420</div>
    <ul class="contacts">
      <li>
        <svg viewBox="0 0 16 16" aria-hidden="true"><path d="M2 5c0-2 2-3 6-3s6 1 6 3v1h-3V5H5v1H2z"/><path d="M3 7h10l1 7H2z"/><circle cx="8" cy="10.5" r="2" fill="#fff"/></svg>
        555 0142 7781
      </li>
      <li>
        <svg viewBox="0 0 16 16" aria-hidden="true"><rect x="4" y="1" width="8" height="14" rx="1.5"/><rect x="5.5" y="3" width="5" height="8" fill="#fff"/></svg>
        555 0196 3024
      </li>
      <li>
        <svg viewBox="0 0 16 16" aria-hidden="true"><rect x="4" y="1" width="8" height="5"/><rect x="1" y="6" width="14" height="9" rx="1"/><rect x="4" y="9" width="8" height="3" fill="#fff"/></svg>
        555 0178 6150
      </li>
      <li>
        <svg viewBox="0 0 16 16" aria-hidden="true"><rect x="1" y="3" width="14" height="10" rx="1"/><path d="M1.5 3.5L8 9l6.5-5.5" stroke="#fff" stroke-width="1.4" fill="none"/></svg>
        marta@vantiqo.com
      </li>
      <li>
        <svg viewBox="0 0 16 16" aria-hidden="true"><circle cx="8" cy="8" r="7"/><path d="M1 8h14M8 1c-3 3-3 11 0 14M8 1c3 3 3 11 0 14" stroke="#fff" stroke-width="1" fill="none"/></svg>
        www.vantiqo.com
      </li>
    </ul>
    <div class="front-disc"></div>
  </section>

</main>
</body>
</html>
```